BUSINESS CARD - HALLORAN FIELD SERVICES

I would like to create a business card for my fertilizer spreading business. I would like to incorporate my existing logo and also a description of the services offered. The business card will be given to farmers so must be kept simple but effective. It will also be left in stores so much also be eye catching in order to stand out from other cards.

Target Market(s)

FARMERS

Requirements
Must have
• FRONT OF CARD = EXISTING LOGO + "CUSTOMISED SPREADING" below the logo

REAR Of CARD = SERVICES OFFERED AND CONTACT DETAILS

- Bulk fertilizer including Lime, Gypsum, Manure & Compost
- Granular fertilizer including Single Super, Urea, Gran-am, & Custom Blends
- Modern equipment - Autosteer & Variable Rate Capable
- Friendly & Reliable Service
- Contact Gus: 0417 552 308
Nice to have
• utilize same color scheme as existing logo

```html
<!DOCTYPE html>
<html lang="en">
<head>
<meta charset="utf-8">
<title>Halloran Field Services – Business Card</title>
<link href="https://fonts.googleapis.com/css2?family=Lato:wght@400;700;900&display=swap" rel="stylesheet">
<style>
  :root {
    --backdrop: #e9eaec;
    --card: #ffffff;
    --ink: #4d4d4f;
    --ink-soft: #5b5b5d;
    --orange: #f5951f;
    --grey-band: #58585a;
    --faint: #f5f5f5;
  }
  * { margin: 0; padding: 0; box-sizing: border-box; }
  html, body {
    width: 1200px; height: 900px; overflow: hidden;
    background: var(--backdrop);
    font-family: "Lato", sans-serif;
  }
  .sheet {
    width: 1200px; height: 900px;
    display: flex; align-items: center; justify-content: center; gap: 40px;
  }
  .card {
    position: relative;
    width: 540px; height: 310px;
    background: var(--card);
    border-radius: 14px;
    overflow: hidden;
    box-shadow: 0 6px 18px rgba(0,0,0,.12);
  }
  /* rear */
  .card-back .edge-bands { position: absolute; inset: 0; }
  .card-back .faint-mark {
    position: absolute; left: 150px; top: 70px;
    width: 200px; height: 200px; border-radius: 50%;
    background: var(--faint);
  }
  .holder { position: absolute; left: 62px; top: 26px; }
  .holder-name { font-size: 21px; font-weight: 700; color: var(--ink); }
  .holder-role { font-size: 14px; color: var(--orange); margin-top: 2px; }
  .services {
    position: absolute; left: 62px; top: 108px;
    list-style: none; font-size: 14.5px; line-height: 1.42; color: var(--ink-soft);
  }
  .services li { position: relative; padding-left: 16px; }
  .services li::before {
    content: ""; position: absolute; left: -2px; top: 5px;
    width: 11px; height: 11px; border-radius: 50%; background: var(--orange);
  }
  .services .cont::before { display: none; }
  .phone {
    position: absolute; right: 34px; bottom: 60px;
    display: flex; align-items: center; gap: 7px;
    font-size: 17px; color: var(--ink);
  }
  .phone svg { width: 16px; height: 16px; }
  /* front */
  .card-front {
    display: flex; flex-direction: column; align-items: center; justify-content: center; gap: 14px;
  }
  .brand { display: flex; align-items: center; gap: 16px; }
  .brand-dot { width: 70px; height: 70px; border-radius: 50%; background: var(--ink); flex: none; }
  .brand-name {
    font-size: 30px; font-weight: 900; color: var(--ink);
    line-height: 1.05; letter-spacing: -0.5px;
  }
  .tagline {
    display: flex; align-items: center; gap: 12px;
    font-size: 17px; font-weight: 700; letter-spacing: 4px;
    color: var(--orange);
  }
  .tagline::before, .tagline::after {
    content: ""; width: 70px; height: 3px; background: var(--orange);
  }
</style>
</head>
<body>
<main class="sheet">
  <section class="card card-back" aria-label="Card rear">
    <svg class="edge-bands" viewBox="0 0 540 310" preserveAspectRatio="none" aria-hidden="true">
      <polygon points="0,80 36,80 36,258 0,290" fill="#f5951f"/>
      <polygon points="0,290 36,258 92,258 92,310 0,310" fill="#58585a"/>
      <polygon points="36,248 92,248 92,258 36,258" fill="#f5951f"/>
    </svg>
    <div class="faint-mark" role="img" aria-label="Faint brand decoration"></div>
    <div class="holder">
      <p class="holder-name">Gus</p>
      <p class="holder-role">ceo / General Manager</p>
    </div>
    <ul class="services">
      <li>Bulk fertilizer including Lime, Gypsum, Manure &amp; Compost.</li>
      <li>Granular fertilizer including Single Super,</li>
      <li class="cont">Urea, Gran-am, &amp; Custom Blends.</li>
      <li>Modern equipment - Autosteer &amp; Variable Rate Capable.</li>
      <li>Friendly &amp; Reliable Service.</li>
    </ul>
    <p class="phone">
      <svg viewBox="0 0 24 24" aria-hidden="true"><path fill="#f5951f" d="M3 8c0-3 4-5 9-5s9 2 9 5v2h-5V8c-1-1-7-1-8 0v2H3zM6 11h12l3 9H3zM12 13a3 3 0 100 6 3 3 0 000-6z"/></svg>
      0417 552 308
    </p>
  </section>

  <section class="card card-front" aria-label="Card front">
    <div class="brand">
      <span class="brand-dot" aria-hidden="true"></span>
      <p class="brand-name">HALLORAN FIELD<br>SERVICES</p>
    </div>
    <p class="tagline">CUSTOMISED SPREADING</p>
  </section>
</main>
</body>
</html>
```